Business Card Design for Vintage Jazz

I am a vintage jazz band leader in New York City. My groups play the music of the 1920s, 1930s and 1940s. My website is morvalquist.com for more info on what I do.

I am looking for a two sided business card design that has the look and feel of a really nice business card from the 1930s. I need to convey with the design that my work has that vintage kind of class and style, but also conveys that we are fun and entertaining.

Most importantly it should make a bold staement. If Hal Denbrook had a card, what would it have looked like? I want a card that I feel confident will make an impact and will let people know that my work is te the top that NYC has to offer in vintage jazz..

Note that I have only decided to avoid the "committed payment" option as I have not used this service before. Assuming that I get quality work I will select a design from those presented.

Target Market(s)

people who want to hire my band for events, media, and new fans of the band

Industry/Entity Type

Performing Art

Contact Information for Business Card

Definitely a matte finish, possibly a sort of old style of paper with that brown tint? definitely a thick card.

Requirements
Must have
• FRONT
• My name: Tobin Vashley
• What I do: Bandleader, Guitarist, Vocalist, Songwriter
• Contact Details: morvalquist.com tobin@morvalquist.com 646-555-0148
• BACK
• My Social Media Links:
• facebook.morvalquist.com
• twitter, instagram, linkedin: morvalquist
• I'm also including a photo image I would like to use. The photo's background is not needed, and to be honest isn't really desireable. Just looking to use the image of me.
Nice to have
• I'm attaching which could be used as is, omitted from the card, or altered maybe with text going around the outside of the circle or in some other way. It may need some clean up to the edges of the lettering as we only use it for the website thumbnail.
• If there's space I'd like to include the text "join our mailing list for a free song download: freesong.morvalquist.com" If not perhaps just "Download a Free Song at: freesong.morvalquist.com - something to this end.
Should not have
• anything cartoony. Don't think retro 90s's vision of the swing era, think actual swing era!
• anything modern. Got to look old school
• Try to avoid dark backgrounds. Since we often play in bars and clubs where it is dar, a d
• avoid script fonts.

```html
<!DOCTYPE html>
<html lang="en">
<head>
<meta charset="utf-8">
<title>Tobin Vashley – Business Card</title>
<link href="https://fonts.googleapis.com/css2?family=Open+Sans:wght@400;600;700&display=swap" rel="stylesheet">
<style>
  :root {
    --stage: #e4e2df;
    --card: #121212;
    --card-back: #0d0d0d;
    --ink: #ffffff;
    --ink-soft: #d6d6d6;
    --rule: #8a8a8a;
    --badge-dark: #2a2a2a;
    --photo-a: #bdbdbd;
    --photo-b: #3c3c3c;
  }
  * { box-sizing: border-box; margin: 0; padding: 0; }
  html, body { width: 1200px; height: 814px; overflow: hidden; }
  body {
    background: var(--stage);
    font-family: "Open Sans", Arial, sans-serif;
    color: var(--ink);
    display: flex;
    align-items: center;
    justify-content: center;
    gap: 48px;
  }
  .card {
    position: relative;
    width: 540px;
    height: 309px;
    border-radius: 4px;
    box-shadow: 0 6px 18px rgba(0,0,0,.25);
    overflow: hidden;
  }
  .card--front { background: var(--card); }
  .card--back { background: var(--card-back); }

  .monogram {
    position: absolute;
    border-radius: 50%;
    display: flex;
    align-items: center;
    justify-content: center;
    text-align: center;
    font-weight: 600;
    line-height: 1.15;
  }
  .card--front .monogram {
    left: 62px; top: 94px; width: 124px; height: 124px;
    background: var(--ink); color: var(--card);
    font-size: 17px;
  }
  .divider {
    position: absolute;
    left: 240px; top: 82px;
    width: 1px; height: 150px;
    background: var(--rule);
  }
  .identity { position: absolute; left: 262px; top: 84px; }
  .identity__name { font-size: 19px; font-weight: 700; letter-spacing: .2px; }
  .identity__roles { font-size: 15px; color: var(--ink-soft); line-height: 1.25; margin-top: 2px; }
  .contact-list { list-style: none; margin-top: 16px; }
  .contact-list li {
    display: flex; align-items: center; gap: 8px;
    font-size: 14px; color: var(--ink-soft); line-height: 1.45;
  }
  .contact-list svg { width: 13px; height: 13px; flex: none; }

  .card--back .monogram {
    left: 40px; top: 26px; width: 96px; height: 96px;
    background: var(--badge-dark); color: var(--ink-soft);
    font-size: 13px;
    box-shadow: inset 0 0 0 2px #3d3d3d;
  }
  .social-list { position: absolute; left: 40px; top: 140px; list-style: none; }
  .social-list li {
    display: flex; align-items: center; gap: 8px;
    font-size: 14px; color: var(--ink-soft); line-height: 1.55;
  }
  .social-list .dot {
    width: 12px; height: 12px; border-radius: 50%;
    background: var(--ink); flex: none;
  }
  .free-song { position: absolute; left: 40px; top: 252px; font-size: 13.5px; color: var(--ink-soft); line-height: 1.3; }
  .free-song strong { color: var(--ink); font-weight: 700; }

  .portrait {
    position: absolute;
    right: 18px; top: 14px;
    width: 230px; height: 250px;
    border-radius: 6px;
    background: radial-gradient(ellipse at 50% 40%, var(--photo-a), var(--photo-b) 75%, transparent 100%);
    opacity: .8;
  }
</style>
</head>
<body>

  <section class="card card--front">
    <div class="monogram">Tobin<br>Vashley</div>
    <div class="divider"></div>
    <div class="identity">
      <h1 class="identity__name">Tobin Vashley</h1>
      <p class="identity__roles">Bandleader, Guitarist<br>Vocalist, Songwriter</p>
      <ul class="contact-list">
        <li>
          <svg viewBox="0 0 13 13" aria-hidden="true"><rect x="3" y="0.5" width="7" height="12" rx="1.2" fill="none" stroke="#fff" stroke-width="1.2"/><circle cx="6.5" cy="10.4" r=".8" fill="#fff"/></svg>
          646-555-0148
        </li>
        <li>
          <svg viewBox="0 0 13 13" aria-hidden="true"><rect x="0.5" y="2.5" width="12" height="8" fill="#fff"/><path d="M0.5 2.5 L6.5 7 L12.5 2.5" fill="none" stroke="#121212" stroke-width="1"/></svg>
          tobin@morvalquist.com
        </li>
        <li>
          <svg viewBox="0 0 13 13" aria-hidden="true"><circle cx="6.5" cy="6.5" r="6" fill="#fff"/><path d="M1 6.5h11M6.5 0.5c-3 3.5-3 8.5 0 12M6.5 0.5c3 3.5 3 8.5 0 12" fill="none" stroke="#121212" stroke-width=".9"/></svg>
          morvalquist.com
        </li>
      </ul>
    </div>
  </section>

  <section class="card card--back">
    <div class="monogram">Tobin<br>Vashley</div>
    <ul class="social-list">
      <li><span class="dot"></span>morvalquist.com</li>
      <li><span class="dot"></span>morvalquist</li>
      <li><span class="dot"></span>morvalquist</li>
      <li><span class="dot"></span>morvalquist</li>
      <li><span class="dot"></span>morvalquist</li>
    </ul>
    <p class="free-song">Download a Free Song at:<br><strong>freesong.morvalquist.com</strong></p>
    <div class="portrait" role="img" aria-label="Black and white photo of the bandleader in a tuxedo tipping a straw boater hat"></div>
  </section>

</body>
</html>
```